Corporate Dinner Invitation – Bold, Professional Look with Subtle Arabic Flair

We are seeking a bold, professional invitation design for a VIP dinner event hosted by Corlan during the TMRE Symposium on Friday, July 18th. This will be used primarily for LinkedIn promotion and as a PDF invitation shared directly with physicians, so it must look clean and polished in portrait orientation.
The design should reflect a high-end corporate aesthetic while still being eye-catching. We’d like to see a very subtle Arabic or Moroccan-inspired design element — think minimal patterns or shapes worked lightly into the background or border. This flair should feel tasteful and restrained, not thematic or decorative. If you need some inspiration for the arabic/morrocan theme - please look up the Zaferan Grill website (https://www.zaferangrl.com/).
Design Guidelines:
Portrait orientation only
Bold, clean, modern layout
Use of both Corlan and KOR Flex TQ brand colors preferred
Use of both Corlan and KOR Flex TQ logos (KOR Flex TQ logo is a subsidiary of the Corlan logo - so please make the Corlan logo the larger of the two; they are both the same company - Corlan owns KOR Flex TQ).
Strong, readable typography that looks professional and commands attention
Design must work well as both a LinkedIn graphic and a standalone PDF
Visual tone: corporate, high-level, medical, innovative
Event Details:
Date: Friday, July 18th
Time: 8:00pm - 10:00pm EST
Location: Zaferan Grill (817 SW Lakeview Ct, Miami, FL 33142)
Speakers: Gerald Hossfeld, MD; Warren Tobique, MD; Kelan Voster, MD (I am including headshots of each speaker - they need to be included on the invite - please remove the backgrounds in the headshot to make all of them uniform looking on the invite)
Final Deliverables:
High-res PDF
PNG or JPEG preview for LinkedIn
Editable source file (Canva, AI or InDesign)
Target Market(s)
Physicians
Industry/Entity Type
Medical Device

```html
<!DOCTYPE html>
<html lang="en">
<head>
<meta charset="utf-8">
<title>Corlan Dinner Night</title>
<link rel="stylesheet" href="https://fonts.googleapis.com/css2?family=Bodoni+Moda:wght@400;500&family=Cormorant+Garamond:wght@400;500&family=Montserrat:wght@400;500;600;700&display=swap">
<style>
  :root {
    --night: #17110f;
    --night-warm: #2a1e1a;
    --rose: #b98f84;
    --rose-light: #d8b7ab;
    --band: #b38f87;
    --band-deep: #9d7870;
    --ink: #2a1a17;
    --cream: #f6ece6;
    --white: #ffffff;
  }
  * { margin: 0; padding: 0; box-sizing: border-box; }
  html, body { width: 739px; height: 1200px; overflow: hidden; background: var(--white); }
  .invite {
    position: relative; width: 739px; height: 1200px; overflow: hidden;
    background: linear-gradient(180deg, var(--night) 0%, var(--night-warm) 60%, var(--night) 66%);
    font-family: "Montserrat", sans-serif;
  }
  .brand-row { position: absolute; top: 34px; left: 0; width: 100%; height: 80px; }
  .brand { position: absolute; color: var(--white); font-family: "Montserrat", sans-serif; font-weight: 600; letter-spacing: 1px; }
  .brand--sub { top: 54px; font-size: 22px; }
  .brand--left { left: 40px; }
  .brand--right { right: 40px; }
  .brand--main { left: 50%; top: 26px; transform: translateX(-50%); font-size: 58px; letter-spacing: 3px; }
  .vertical-note {
    position: absolute; top: 150px; color: rgba(255,255,255,0.45);
    font-size: 10px; letter-spacing: 1.5px; white-space: nowrap;
  }
  .vertical-note--left { left: 48px; transform-origin: left top; transform: rotate(-90deg) translateX(-330px); }
  .vertical-note--right { right: 48px; transform-origin: right top; transform: rotate(90deg) translateX(230px); }
  .invite-line { position: absolute; top: 206px; width: 100%; text-align: center; color: var(--rose-light); font-size: 13px; font-weight: 600; letter-spacing: 5px; }
  .invite-sub { position: absolute; top: 230px; width: 100%; display: flex; justify-content: center; align-items: center; gap: 12px; color: rgba(216,183,171,0.7); font-size: 9px; letter-spacing: 2px; }
  .invite-sub::before, .invite-sub::after { content: ""; width: 70px; height: 1px; background: rgba(216,183,171,0.5); }
  .title { position: absolute; width: 100%; text-align: center; color: var(--rose); font-family: "Bodoni Moda", serif; font-weight: 400; line-height: 1; z-index: 3; }
  .title--first { top: 246px; font-size: 120px; letter-spacing: -2px; }
  .title--second { top: 374px; font-size: 74px; }
  .speaker-photos { position: absolute; top: 480px; left: 90px; width: 560px; height: 307px; display: flex; justify-content: space-between; align-items: flex-end; z-index: 2; }
  .speaker-photo { width: 178px; height: 100%; border-radius: 90px 90px 0 0; background: linear-gradient(180deg, #8b7a70 0%, #d9d4cf 45%, #3d4a66 100%); }
  .speaker-photo--center { width: 200px; height: 320px; background: linear-gradient(180deg, #9a7a66 0%, #c4a48f 35%, #2f3f63 100%); }
  .details { position: absolute; top: 787px; left: 0; width: 100%; height: 413px; background: linear-gradient(180deg, var(--band) 0%, var(--band-deep) 100%); text-align: center; }
  .speakers-label { margin-top: 34px; color: var(--ink); font-size: 22px; font-weight: 700; letter-spacing: 1px; }
  .speaker-list { list-style: none; margin-top: 6px; color: var(--ink); font-size: 22px; font-weight: 500; line-height: 30px; }
  .event-date { margin-top: 40px; color: var(--cream); font-family: "Cormorant Garamond", serif; font-size: 34px; font-weight: 500; }
  .event-time { margin-top: 4px; color: var(--cream); font-family: "Cormorant Garamond", serif; font-size: 26px; }
  .venue { margin-top: 14px; color: var(--cream); font-family: "Cormorant Garamond", serif; font-size: 19px; line-height: 24px; }
  .palm { position: absolute; bottom: 0; }
  .palm--left { left: 0; width: 150px; height: 230px; }
  .palm--right { right: 0; width: 120px; height: 200px; }
</style>
</head>
<body>
<main class="invite">
  <header class="brand-row">
    <span class="brand brand--sub brand--left">KOR FLEX TQ</span>
    <span class="brand brand--main">CORLAN</span>
    <span class="brand brand--sub brand--right">KOR DINNER</span>
  </header>

  <p class="vertical-note vertical-note--left">Zaferan Grill · 817 SW Lakeview Ct, Miami, FL 33142</p>
  <p class="vertical-note vertical-note--right">#Corlan dinner night</p>

  <p class="invite-line">PLEASE JOIN US FOR</p>
  <p class="invite-sub">an exclusive evening</p>

  <h1 class="title title--first">Dinner</h1>
  <p class="title title--second">Night</p>

  <div class="speaker-photos">
    <div class="speaker-photo" role="img" aria-label="Headshot of Gerald Hossfeld, MD in a white coat"></div>
    <div class="speaker-photo speaker-photo--center" role="img" aria-label="Headshot of Warren Tobique, MD in a navy blazer"></div>
    <div class="speaker-photo" role="img" aria-label="Headshot of Kelan Voster, MD in a white coat"></div>
  </div>

  <section class="details">
    <p class="speakers-label">SPEAKERS:</p>
    <ul class="speaker-list">
      <li>MD; GERALD HOSSFELD,</li>
      <li>MD; WARREN TOBIQUE</li>
      <li>MD; KELAN VOSTER</li>
    </ul>
    <p class="event-date">Friday, July 18th</p>
    <p class="event-time">8:00pm – 10:00pm EST</p>
    <p class="venue">Zaferan Grill<br>(817 SW Lakeview Ct, Miami, FL, 33142)</p>

    <svg class="palm palm--left" viewBox="0 0 150 230" role="img" aria-label="Line illustration of palm trees and a camel">
      <rect width="150" height="230" fill="var(--band-deep)" opacity="0.5"/>
    </svg>
    <svg class="palm palm--right" viewBox="0 0 120 200" role="img" aria-label="Line illustration of palm trees">
      <rect width="120" height="200" fill="var(--band-deep)" opacity="0.5"/>
    </svg>
  </section>
</main>
</body>
</html>
```